Orvane Thinner Logo and Packaging Design

We are seeking a striking and professional logo and packaging design for our new product line, Orvane Thinner. This logo will be used on the packaging for three different sizes of half-transparent carboys: 1L, 4L, and 20L. Orvane Thinner is a high-quality solvent brand known for its excellent solvency, fast-drying properties, and pleasant smell. The logo should feature an eagle motif to symbolize power and precision, and our slogan, "RISE IN PURITY." The design should be suitable for placement on hardware store and warehouse shelves. Additionally, we need the designer to create an eagle logo to accompany the packaging.

Packaging Dimensions:
1L Carboy:
Front: 71mm height x 142mm width
Side: 71mm height x 73mm width
4L Carboy:
Front: 160mm height x 170mm width
Side: 160mm height x 120mm width
20L Carboy:
Front: 245mm height x 190mm width
Side: 215mm height x 190mm width
Front Label Requirements:

Product Name: Thinner QXR
Volume: 20L
Precautionary Statements:
Keep Away from Sources of ignition - No Smoking
Avoid Contact with Eyes
Do Not Empty into Drains or Sewers
Take Precautionary Measures Against Static Discharge
Hazard Statements:
Flammable Liquid and Vapor
May be fatal if swallowed or enters Airways
Causes Skin Irritation
Causes Serious Eye Irritation
Causes Damage to Organs if Prolonged or Repeated Exposure
Hazard Pictograms: (Include relevant hazard symbols)
Design Requirements:

Logo: Eagle motif (to be designed by the designer)
Slogan: RISE IN PURITY
Color Scheme: Designer to recommend (should be striking and professional for retail display)

Please see my latest picture. Kindly note the packaging is in Plastic Carboy (not in metal tin as per PS).

Eagle to be more majestic and bigger (as if soaring in the sky).
Singapore landscape as background to have Singapore identity such as KTR, Corvale wheel, terrace at the cove etc.

Eagle to be more majestic and bigger, wings to spread wide.
We not want it to be of photo style, but more on a cartoon style. Please see my latest file uploaded.

Target Market(s)

Our target market includes painting companies, construction companies, direct household consumers, and industrial users who require high-quality solvents for various applications.

Industry/Entity Type

Chemical, spray paint and painting, household, industrial

Requirements
Must have
• Professional and Striking Design: Eye-catching and professional packaging for retail shelves. Eagle Logo: A strong, precise eagle logo. Slogan: "RISE IN PURITY" prominently displayed. Clear Precautionary and Hazard Statements: Important safety information and pictograms. Volume Indication: Clearly marked (e.g., 1L, 4L, 20L). Eagle to be more majestic and bigger (as if soaring in the sky). Singapore landscape as background to have Singapore identity such as KTR, Corvale wheel, terrace at the cove etc.
Nice to have
• Color Scheme Recommendations: Suggestions for a professional, striking color scheme. Versatility: Design elements adaptable across different sizes of packaging. Environmentally Friendly Elements: Indications of sustainability or eco-friendliness in the design.
Should not have
• Overly Complex Designs: Avoid cluttered or overly intricate designs that detract from readability. Inconsistent Branding: Ensure all elements are cohesive and align with the brand identity.

```html
<!DOCTYPE html>
<html lang="en">
<head>
<meta charset="utf-8">
<title>Orvane Thinner – Label Range</title>
<link href="https://fonts.googleapis.com/css2?family=Montserrat:wght@500;600;700;800;900&display=swap" rel="stylesheet">
<style>
  :root{
    --board:#bdbbbc;
    --ink:#111111;
    --white:#ffffff;
    --green-a:#3aa93a;
    --green-b:#2fb0ad;
    --orange-a:#e0851f;
    --pink-b:#ea5590;
    --violet-a:#8e68b4;
    --blue-b:#3f9bd9;
    --accent-green:#2fb456;
    --accent-orange:#e88a1a;
    --accent-violet:#7d70c2;
  }
  *{margin:0;padding:0;box-sizing:border-box}
  html,body{width:1200px;height:569px;overflow:hidden;background:var(--board)}
  body{font-family:'Montserrat',sans-serif;position:relative}
  .range{position:absolute;left:282px;top:81px;width:636px;height:406px}
  .label{position:absolute;overflow:hidden;color:var(--ink)}
  .label--20l{left:0;top:0;width:314px;height:406px;background:linear-gradient(135deg,var(--green-a) 0%,#34ad6a 45%,var(--green-b) 100%)}
  .label--1l{left:351px;top:0;width:236px;height:117px;background:linear-gradient(110deg,var(--orange-a) 0%,#e8736a 55%,var(--pink-b) 100%)}
  .label--4l{left:352px;top:134px;width:284px;height:266px;background:linear-gradient(30deg,var(--violet-a) 0%,#6c8ad0 55%,var(--blue-b) 100%)}

  .brand-band{position:absolute;top:0;bottom:0;background:var(--ink)}
  .brand-disc{position:absolute;border-radius:50%;background:var(--ink)}
  .brand-name{position:absolute;left:0;right:0;text-align:center;color:var(--white);font-weight:800;line-height:1.02}
  .brand-rule{position:absolute;height:3px}
  .eco-badge{position:absolute;border-radius:50%}
  .volume{position:absolute;left:0;right:0;text-align:center;color:var(--white);font-weight:900;letter-spacing:.02em}
  .backdrop-eagle{position:absolute;border-radius:50% 50% 0 0;background:radial-gradient(ellipse at 50% 60%,rgba(255,255,255,.28) 0%,rgba(255,255,255,.1) 55%,rgba(255,255,255,0) 75%)}

  .title{position:absolute;font-weight:900;line-height:1;text-transform:uppercase;white-space:nowrap}
  .title .dark{color:var(--ink);display:block}
  .title .light{color:var(--white);display:block}
  .safety{position:absolute;white-space:nowrap}
  .safety h3{color:var(--white);font-weight:800;text-transform:uppercase}
  .safety ul{list-style:none;font-weight:600}
  .safety li{position:relative}
  .safety li::before{content:"";position:absolute;border-radius:50%;background:var(--ink)}
  .pictos{position:absolute;display:flex}
  .pictos svg{display:block}

  /* 20 L */
  .label--20l .brand-band{left:21px;width:75px}
  .label--20l .brand-disc{left:12px;top:12px;width:90px;height:90px}
  .label--20l .brand-name{top:88px;left:21px;width:75px;font-size:12.5px}
  .label--20l .brand-rule{left:48px;top:120px;width:20px;background:var(--accent-green)}
  .label--20l .eco-badge{left:36px;top:201px;width:44px;height:44px;border:2px solid var(--accent-green)}
  .label--20l .volume{left:21px;width:75px;top:362px;font-size:25px}
  .label--20l .backdrop-eagle{left:80px;top:250px;width:240px;height:160px}
  .label--20l .title{left:119px;top:30px;font-size:33px}
  .label--20l .safety{left:119px;top:173px;font-size:6.3px;line-height:7.3px}
  .label--20l .safety h3{font-size:7px;line-height:8px}
  .label--20l .safety .hazards{margin-top:7px}
  .label--20l .safety li::before{left:-6px;top:2.6px;width:2.4px;height:2.4px}
  .label--20l .pictos{left:187px;top:349px;gap:2px}

  /* 1 L */
  .label--1l .brand-band{left:9px;width:46px}
  .label--1l .brand-disc{left:8px;top:-6px;width:52px;height:52px}
  .label--1l .brand-name{top:37px;left:9px;width:46px;font-size:7px}
  .label--1l .brand-rule{left:26px;top:56px;width:11px;height:2px;background:var(--accent-orange)}
  .label--1l .eco-badge{left:22px;top:64px;width:24px;height:24px;border:1.4px solid var(--accent-orange)}
  .label--1l .volume{left:9px;width:46px;top:95px;font-size:13px}
  .label--1l .backdrop-eagle{left:80px;top:40px;width:140px;height:80px}
  .label--1l .title{left:69px;top:10px;font-size:15px;letter-spacing:-.2px}
  .label--1l .safety{left:69px;top:50px;font-size:3.6px;line-height:4.6px}
  .label--1l .safety h3{font-size:4px;line-height:5px}
  .label--1l .safety .hazards{margin-top:4px}
  .label--1l .safety li::before{left:-3px;top:1.6px;width:1.4px;height:1.4px}
  .label--1l .pictos{left:209px;top:47px;flex-direction:column;gap:1px}

  /* 4 L */
  .label--4l .brand-band{left:19px;width:68px}
  .label--4l .brand-disc{left:13px;top:2px;width:82px;height:82px}
  .label--4l .brand-name{top:76px;left:19px;width:68px;font-size:11.5px}
  .label--4l .brand-rule{left:44px;top:105px;width:18px;background:var(--accent-violet)}
  .label--4l .eco-badge{left:34px;top:151px;width:40px;height:40px;border:2px solid var(--accent-violet)}
  .label--4l .volume{left:19px;width:68px;top:227px;font-size:23px}
  .label--4l .backdrop-eagle{left:90px;top:120px;width:200px;height:150px}
  .label--4l .title{left:108px;top:18px;font-size:29px}
  .label--4l .safety{left:108px;top:132px;font-size:5.6px;line-height:6.6px}
  .label--4l .safety h3{font-size:6.3px;line-height:7.4px}
  .label--4l .safety .hazards{margin-top:5px}
  .label--4l .safety ul{color:#1c1d3a}
  .label--4l .safety li::before{left:-5px;top:2.4px;width:2px;height:2px}
  .label--4l .pictos{left:168px;top:223px;gap:3px}
</style>
</head>
<body>
<svg width="0" height="0" style="position:absolute" aria-hidden="true">
  <defs>
    <symbol id="ghs-flame" viewBox="0 0 100 100">
      <polygon points="50,5 95,50 50,95 5,50" fill="none" stroke="#111" stroke-width="7" stroke-linejoin="miter"/>
      <path d="M50 27C58 39 66 46 64 60C63 70 56 75 50 75C43 75 36 70 36 61C36 52 42 48 44 40C47 46 48 50 52 52C53 44 52 36 50 27Z" fill="#111"/>
    </symbol>
    <symbol id="ghs-exclaim" viewBox="0 0 100 100">
      <polygon points="50,5 95,50 50,95 5,50" fill="none" stroke="#111" stroke-width="7"/>
      <rect x="45.5" y="27" width="9" height="31" rx="2" fill="#111"/>
      <circle cx="50" cy="68" r="5" fill="#111"/>
    </symbol>
    <symbol id="ghs-health" viewBox="0 0 100 100">
      <polygon points="50,5 95,50 50,95 5,50" fill="none" stroke="#111" stroke-width="7"/>
      <circle cx="50" cy="33" r="7.5" fill="#111"/>
      <path d="M33 73C33 53 40 44 50 44C60 44 67 53 67 73Z" fill="#111"/>
      <polygon points="50,51 53,58 60,58 54.5,62 57,69 50,65 43,69 45.5,62 40,58 47,58" fill="#fff"/>
    </symbol>
  </defs>
</svg>

<main class="range">

  <!-- 20 L front label -->
  <section class="label label--20l">
    <div class="backdrop-eagle" role="img" aria-label="Faint soaring eagle illustration"></div>
    <div class="brand-band"></div>
    <div class="brand-disc"></div>
    <p class="brand-name">ORVANE<br>THINNER</p>
    <div class="brand-rule"></div>
    <div class="eco-badge" role="img" aria-label="Eco friendly badge"></div>
    <p class="volume">20 L</p>
    <h1 class="title"><span class="dark">Thinner</span><span class="dark">QXR</span><span class="light">Rise in</span><span class="light">Purity</span></h1>
    <div class="safety">
      <h3>Precautions</h3>
      <ul>
        <li>Keep Away from Sources of ignition - No Smoking</li>
        <li>Avoid Contact with Eyes</li>
        <li>Do Not Empty into Drains or Sewers</li>
        <li>Take Precautionary Measures Against Static Discharge</li>
      </ul>
      <h3 class="hazards">Hazards</h3>
      <ul>
        <li>Flammable Liquid and Vapor</li>
        <li>May be fatal if swallowed or enters Airways</li>
        <li>Causes Skin Irritation</li>
        <li>Causes Serious Eye Irritation</li>
        <li>Causes Damage to Organs if Prolonged or<br>Repeated Exposure</li>
      </ul>
    </div>
    <div class="pictos">
      <svg width="36" height="36" role="img" aria-label="Flammable"><use href="#ghs-flame"/></svg>
      <svg width="36" height="36" role="img" aria-label="Irritant"><use href="#ghs-exclaim"/></svg>
      <svg width="36" height="36" role="img" aria-label="Health hazard"><use href="#ghs-health"/></svg>
    </div>
  </section>

  <!-- 1 L front label -->
  <section class="label label--1l">
    <div class="backdrop-eagle" role="img" aria-label="Faint soaring eagle illustration"></div>
    <div class="brand-band"></div>
    <div class="brand-disc"></div>
    <p class="brand-name">ORVANE<br>THINNER</p>
    <div class="brand-rule"></div>
    <div class="eco-badge" role="img" aria-label="Eco friendly badge"></div>
    <p class="volume">1 L</p>
    <h1 class="title"><span class="dark">Thinner QXR</span><span class="light">Rise in Purity</span></h1>
    <div class="safety">
      <h3>Precautions</h3>
      <ul>
        <li>Keep Away from Sources of ignition - No Smoking</li>
        <li>Avoid Contact with Eyes</li>
        <li>Do Not Empty into Drains or Sewers</li>
        <li>Take Precautionary Measures Against Static Discharge</li>
      </ul>
      <h3 class="hazards">Hazards</h3>
      <ul>
        <li>Flammable Liquid and Vapor</li>
        <li>May be fatal if swallowed or enters Airways</li>
        <li>Causes Skin Irritation</li>
        <li>Causes Serious Eye Irritation</li>
        <li>Causes Damage to Organs if Prolonged or<br>Repeated Exposure</li>
      </ul>
    </div>
    <div class="pictos">
      <svg width="20" height="20" role="img" aria-label="Flammable"><use href="#ghs-flame"/></svg>
      <svg width="20" height="20" role="img" aria-label="Irritant"><use href="#ghs-exclaim"/></svg>
      <svg width="20" height="20" role="img" aria-label="Health hazard"><use href="#ghs-health"/></svg>
    </div>
  </section>

  <!-- 4 L front label -->
  <section class="label label--4l">
    <div class="backdrop-eagle" role="img" aria-label="Faint soaring eagle illustration"></div>
    <div class="brand-band"></div>
    <div class="brand-disc"></div>
    <p class="brand-name">ORVANE<br>THINNER</p>
    <div class="brand-rule"></div>
    <div class="eco-badge" role="img" aria-label="Eco friendly badge"></div>
    <p class="volume">4 L</p>
    <h1 class="title"><span class="dark">Thinner</span><span class="dark">QXR</span><span class="light">Rise in</span><span class="light">Purity</span></h1>
    <div class="safety">
      <h3>Precautions</h3>
      <ul>
        <li>Keep Away from Sources of ignition - No Smoking</li>
        <li>Avoid Contact with Eyes</li>
        <li>Do Not Empty into Drains or Sewers</li>
        <li>Take Precautionary Measures Against Static Discharge</li>
      </ul>
      <h3 class="hazards">Hazards</h3>
      <ul>
        <li>Flammable Liquid and Vapor</li>
        <li>May be fatal if swallowed or enters Airways</li>
        <li>Causes Skin Irritation</li>
        <li>Causes Serious Eye Irritation</li>
        <li>Causes Damage to Organs if Prolonged or<br>Repeated Exposure</li>
      </ul>
    </div>
    <div class="pictos">
      <svg width="32" height="32" role="img" aria-label="Flammable"><use href="#ghs-flame"/></svg>
      <svg width="32" height="32" role="img" aria-label="Irritant"><use href="#ghs-exclaim"/></svg>
      <svg width="32" height="32" role="img" aria-label="Health hazard"><use href="#ghs-health"/></svg>
    </div>
  </section>

</main>
</body>
</html>
```